Medical Clinic Group Looking for Website Design

We own and operate medical clinics and are looking looking to revamp our website. Our current website is www.brightpathcareclinics.ca We need our website to be more functional, user friendly, and easier to maintain.

```html
<!DOCTYPE html>
<html lang="en">
<head>
<meta charset="utf-8">
<title>Brightpath Care Clinics</title>
<link href="https://fonts.googleapis.com/css2?family=Jost:wght@400;500;600&family=Oswald:wght@400;500&display=swap" rel="stylesheet">
<style>
:root{
  --teal:#35cfd9;
  --gray-bar:#6d6e71;
  --gray-foot:#808184;
  --ink:#3d3d3f;
  --muted:#6a6a6c;
  --white:#ffffff;
}
*{box-sizing:border-box;margin:0;padding:0}
html,body{width:1200px;height:2643px;overflow:hidden;background:var(--white)}
body{font-family:"Jost",sans-serif;color:var(--ink);position:relative}
.abs{position:absolute}
.btn{position:absolute;background:var(--teal);color:var(--white);font-family:"Jost",sans-serif;font-weight:600;font-size:13px;letter-spacing:.5px;text-transform:uppercase;display:flex;align-items:center;justify-content:center;border-radius:26px 26px 0 26px}

.topbar{left:0;top:0;width:1200px;height:41px;background:var(--gray-bar);color:var(--white);font-size:14px}
.topbar .item{position:absolute;top:11px;display:flex;align-items:center;gap:10px}
.topbar .sep{position:absolute;left:250px;top:9px;font-size:16px}
.social{position:absolute;display:flex;gap:7px}
.social span{width:32px;height:32px;border-radius:50%;background:#a2a3a6;display:block}
.social span:first-child{background:var(--white)}

.brand{position:absolute;display:flex;align-items:center;gap:12px;font-family:"Jost",sans-serif;font-weight:400;font-size:30px;color:var(--teal)}
.brand .dot{width:30px;height:30px;border-radius:50%;border:3px solid var(--gray-bar)}
.nav{position:absolute;left:465px;top:80px;display:flex;gap:22px;font-size:16px;color:var(--ink);font-weight:500}
.nav .active{color:var(--teal)}

.hero{left:0;top:137px;width:1200px;height:557px;border-radius:150px 130px 0 90px;overflow:hidden;background:linear-gradient(100deg,#8f8a88 0%,#c9bfb6 35%,#e9e3dc 60%,#f1eeea 100%)}
.hero-photo{position:absolute;inset:0}
.hero-title{left:753px;top:296px;font-family:"Oswald",sans-serif;font-weight:500;font-size:39px;line-height:48px;color:#3a3a3c;letter-spacing:.5px}
.hero-sub{left:754px;top:400px;font-size:21px;line-height:31px;color:#3a3a3c;font-weight:500}

.section-title{position:absolute;left:0;width:1200px;text-align:center;font-family:"Oswald",sans-serif;font-weight:400;font-size:43px;color:#4a4a4c}
.section-title b{color:var(--teal);font-weight:400}
.section-text{position:absolute;text-align:center;font-size:17.5px;line-height:29px;color:var(--muted);letter-spacing:.2px}

.split{top:1095px;width:600px;height:471px;overflow:hidden}
.split.patients{left:0;border-radius:140px 0 0 0;background:linear-gradient(120deg,#3e4654,#2f3746 55%,#3f4757)}
.split.providers{left:600px;border-radius:0 140px 140px 0;background:linear-gradient(120deg,#2bc6cd,#1aa5a9 55%,#0f6f72)}
.split .icon{position:absolute;left:251px;top:158px;width:98px;height:98px;border-radius:50%;border:2px solid var(--white);display:flex;align-items:center;justify-content:center}
.split .label{position:absolute;left:0;width:600px;top:285px;text-align:center;color:var(--white);font-weight:600;font-size:30px;letter-spacing:.5px}

.clinic{top:1823px;width:309px;height:360px;overflow:hidden}
.clinic .label{position:absolute;left:0;bottom:30px;width:100%;text-align:center;color:var(--white);font-weight:600;font-size:18px;letter-spacing:.5px}
.clinic.one{left:111px;border-radius:60px 0 0 60px;background:linear-gradient(160deg,#c9b2a5,#6d5a50 45%,#2c2c33)}
.clinic.two{left:445px;border-radius:60px 0 60px 0;background:linear-gradient(150deg,#3fd3dc,#2cc0c9 60%,#35cfd9)}
.clinic.three{left:780px;border-radius:60px 60px 0 60px;background:linear-gradient(160deg,#5d5f62,#d8d3cf 45%,#f1ede9)}

.footer{left:0;top:2292px;width:1200px;height:351px;background:var(--gray-foot);border-radius:0 110px 0 0;color:var(--white)}
.footer h4{position:absolute;top:58px;font-size:17px;font-weight:600;letter-spacing:.3px}
.footer .links{position:absolute;left:385px;top:102px;list-style:none;font-size:14px}
.footer .links li{height:34.3px;display:flex;align-items:center;gap:22px}
.footer .links li i{width:13px;height:13px;border-radius:50%;background:var(--teal);display:block;position:relative}
.footer .links li i::after{content:"";position:absolute;left:4px;top:3.5px;border-left:5px solid var(--gray-foot);border-top:3px solid transparent;border-bottom:3px solid transparent}
.footer .field{position:absolute;left:548px;top:141px;width:275px;height:46px;background:var(--white);border-radius:23px 23px 0 23px;color:#8a8a8c;font-size:14px;padding:14px 17px}
.footer .contact{position:absolute;left:862px;font-size:14px;display:flex;gap:22px;line-height:24px}
.footer .contact svg{flex:none;margin-top:4px}
.footer .rule{position:absolute;left:111px;top:284px;width:977px;height:1px;background:#9a9b9e}
.footer .copy{position:absolute;left:458px;top:316px;font-size:12px}
</style>
</head>
<body>

<div class="abs topbar">
  <div class="item" style="left:111px">
    <svg width="13" height="13" viewBox="0 0 24 24"><path fill="#35cfd9" d="M6.6 10.8a15.1 15.1 0 0 0 6.6 6.6l2.2-2.2c.3-.3.7-.4 1-.2 1.1.4 2.3.6 3.6.6.6 0 1 .4 1 1V20c0 .6-.4 1-1 1A17 17 0 0 1 3 4c0-.6.4-1 1-1h3.5c.6 0 1 .4 1 1 0 1.3.2 2.5.6 3.6.1.3 0 .7-.2 1z"/></svg>
    <span>555.014.2290</span>
  </div>
  <div class="sep">|</div>
  <div class="item" style="left:274px">
    <svg width="15" height="12" viewBox="0 0 24 18"><path fill="#35cfd9" d="M0 0h24v2L12 10 0 2zM0 5l12 8 12-8v13H0z"/></svg>
    <span>hello@brightpathcareclinics.ca</span>
  </div>
  <div class="social" style="left:979px;top:5px"><span></span><span></span><span></span></div>
</div>

<div class="brand" style="left:111px;top:68px"><span class="dot"></span>Brightpath Care</div>
<nav class="nav">
  <span class="active">Home</span><span>For Patients</span><span>For Providers</span><span>About Us</span><span>Locations</span>
</nav>
<div class="btn" style="left:943px;top:67px;width:145px;height:46px">Book Online</div>

<section class="abs hero">
  <div class="hero-photo" role="img" aria-label="Photo of a young woman hugging a smiling senior woman in a bright living room"></div>
</section>
<h1 class="abs hero-title">EASY ACCESS TO CARE<br>WHEN YOU NEED IT</h1>
<p class="abs hero-sub">Online appointment booking now<br>available to all patients</p>
<div class="btn" style="left:754px;top:481px;width:188px;height:46px">Book Appointment</div>

<h2 class="section-title" style="top:770px"><b>About</b> Us</h2>
<p class="section-text" style="left:125px;top:852px;width:950px">At Brightpath Care Clinics, work/life balance is at the core of our culture. Our philosophy is simple: we take exceptional care of our people so that they can take exceptional care of our patients. Contact us to find out why so many healthcare providers and medical professionals have chosen to join our team.</p>
<div class="btn" style="left:531px;top:970px;width:138px;height:47px">Learn More</div>

<div class="abs split patients" role="img" aria-label="Photo of a doctor in scrubs comforting a senior male patient">
  <div class="icon">
    <svg width="44" height="44" viewBox="0 0 44 44" fill="none" stroke="#fff" stroke-width="2"><rect x="8" y="6" width="26" height="30" rx="2"/><rect x="14" y="18" width="20" height="20" rx="2"/><path d="M24 22v12M18 28h12"/></svg>
  </div>
  <div class="label">FOR PATIENTS</div>
</div>
<div class="abs split providers" role="img" aria-label="Photo of a provider working with a calculator at a desk, teal tinted">
  <div class="icon">
    <svg width="48" height="48" viewBox="0 0 48 48" fill="none" stroke="#fff" stroke-width="2"><circle cx="28" cy="16" r="8"/><circle cx="28" cy="16" r="3"/><path d="M6 32h8l10 4h12l6-6M14 30v12H6"/></svg>
  </div>
  <div class="label">FOR PROVIDERS</div>
</div>

<h2 class="section-title" style="top:1648px"><b>Book</b> Now</h2>
<p class="section-text" style="left:150px;top:1725px;width:900px">Brightpath Care Clinics continues to create options that better suit your lifestyle. Book your appointment when it's convenient for you, even if you don't have a family doctor.</p>

<div class="abs clinic one" role="img" aria-label="Photo of a therapist examining a patient's knee"><div class="label">RIDGEVIEW MEDICAL</div></div>
<div class="abs clinic two" role="img" aria-label="Photo of a smiling doctor with a tablet talking to a patient, teal tinted"><div class="label">WESTBANK</div></div>
<div class="abs clinic three" role="img" aria-label="Photo of a doctor in a white coat writing notes at a desk"><div class="label">CEDAR COVE MEDICAL</div></div>

<footer class="abs footer">
  <div class="brand" style="left:111px;top:142px;color:#fff"><span class="dot" style="border-color:#fff"></span>Brightpath Care</div>

  <h4 style="left:385px">USEFUL LINKS</h4>
  <ul class="links">
    <li><i></i>Home</li><li><i></i>For Patients</li><li><i></i>For Providers</li><li><i></i>About Us</li><li><i></i>Locations</li>
  </ul>

  <h4 style="left:548px">NEWSLETTER</h4>
  <div class="abs" style="left:548px;top:104px;font-size:14px">Subscribe To Our Newsletter</div>
  <div class="field">Email Address</div>
  <div class="btn" style="left:548px;top:195px;width:129px;height:46px">Subscribe</div>

  <h4 style="left:862px">CONTACT US</h4>
  <div class="contact" style="top:99px">
    <svg width="13" height="13" viewBox="0 0 24 24"><path fill="#35cfd9" d="M6.6 10.8a15.1 15.1 0 0 0 6.6 6.6l2.2-2.2c.3-.3.7-.4 1-.2 1.1.4 2.3.6 3.6.6.6 0 1 .4 1 1V20c0 .6-.4 1-1 1A17 17 0 0 1 3 4c0-.6.4-1 1-1h3.5c.6 0 1 .4 1 1 0 1.3.2 2.5.6 3.6.1.3 0 .7-.2 1z"/></svg>
    <span>555.014.2290</span>
  </div>
  <div class="contact" style="top:132px">
    <svg width="15" height="12" viewBox="0 0 24 18"><path fill="#35cfd9" d="M0 0h24v2L12 10 0 2zM0 5l12 8 12-8v13H0z"/></svg>
    <span>hello@brightpathcareclinics.ca</span>
  </div>
  <div class="contact" style="top:163px">
    <svg width="12" height="15" viewBox="0 0 20 26"><path fill="#35cfd9" d="M10 0a10 10 0 0 0-10 10c0 7 10 16 10 16s10-9 10-16A10 10 0 0 0 10 0zm0 14a4 4 0 1 1 0-8 4 4 0 0 1 0 8z"/></svg>
    <span>2040 Lakeview Rd, Lake Country,<br>BC V0H 1A0, Canada</span>
  </div>

  <div class="rule"></div>
  <div class="copy">© 2022 Brightpath Care Clinics &nbsp;|&nbsp; All Rights Reserved</div>
  <div class="social" style="left:979px;top:308px"><span style="background:var(--teal)"></span><span style="background:#fff"></span><span style="background:#fff"></span></div>
</footer>

</body>
</html>
```